Business Card Design Project

We have 2 businesses which help each other.

Brightvale Care (providing nurses to hospitals/nursing homes etc)

and

Brightvale HR (providing nurses to our brightvale care business - but also providing workers for farms, restaurants meatworks etc)

We would like 2 separate business cards - but similar design and feel

Target Market(s)

Managers of nursing homes, hospitals, farms, meatworks, restauants

Industry/Entity Type

Business

Requirements
Must have
• both logos
https://www.filequay-example.com/s/6v4i7j2fzkpw8wx/BrightvaleHR-Logo-Horizontal.ai
https://www.filequay-example.com/s/dr33nlhq82w3z6t/46051_844932_40145_sourcefile.ai

You may edit the layout of Brightvale HR logo

Name
position
mobile
Phone
name@brightvalehr.com.au
brigthvalehr.com.au

Name
position
mobile
phone
name@brightvalecare.net.au
brightvalecare.net.au

```html
<!DOCTYPE html>
<html lang="en">
<head>
<meta charset="utf-8">
<title>Brightvale Care and Brightvale HR — Business Cards</title>
<link href="https://fonts.googleapis.com/css2?family=Quicksand:wght@500;600;700&display=swap" rel="stylesheet">
<style>
  :root {
    --navy: #2f2a80;
    --sky: #45ade3;
    --sky-deep: #3a9bd6;
    --ink: #2b2b2b;
    --paper: #ffffff;
    --backdrop: #e6eaec;
  }
  * { box-sizing: border-box; margin: 0; padding: 0; }
  html, body {
    width: 1200px;
    height: 960px;
    overflow: hidden;
    background: var(--backdrop);
    font-family: "Quicksand", sans-serif;
  }
  .canvas {
    width: 1200px;
    height: 960px;
    display: flex;
    flex-direction: column;
    align-items: center;
    justify-content: center;
    gap: 64px;
  }
  .card-row {
    display: flex;
    gap: 40px;
  }
  .card {
    width: 560px;
    height: 320px;
    border-radius: 4px;
    box-shadow: 0 6px 18px rgba(0, 0, 0, 0.12);
    position: relative;
    overflow: hidden;
  }
  .card-back {
    background: linear-gradient(160deg, var(--sky) 0%, var(--sky-deep) 100%);
  }
  .card-front {
    background: var(--paper);
  }
  .brand {
    position: absolute;
    left: 34px;
    top: 144px;
    display: flex;
    align-items: center;
    gap: 10px;
  }
  .brand-dot {
    width: 14px;
    height: 14px;
    border-radius: 50%;
    background: var(--sky);
    flex: none;
  }
  .brand-name {
    font-size: 25px;
    font-weight: 700;
    color: var(--navy);
    letter-spacing: -0.2px;
    white-space: nowrap;
  }
  .divider {
    position: absolute;
    left: 282px;
    top: 28px;
    width: 2px;
    height: 264px;
    background: linear-gradient(180deg, rgba(69,173,227,0) 0%, var(--sky) 45%, rgba(69,173,227,0) 100%);
  }
  .contact {
    position: absolute;
    left: 304px;
    top: 40px;
    right: 16px;
  }
  .person-name {
    font-size: 19px;
    font-weight: 700;
    color: var(--sky);
    letter-spacing: 0.3px;
  }
  .person-role {
    font-size: 17px;
    font-weight: 500;
    color: var(--ink);
    letter-spacing: 0.5px;
    margin-top: 2px;
  }
  .contact-list {
    list-style: none;
    margin-top: 32px;
    display: flex;
    flex-direction: column;
    gap: 11px;
  }
  .contact-item {
    display: flex;
    align-items: center;
    gap: 9px;
    font-size: 13px;
    font-weight: 600;
    color: var(--ink);
    letter-spacing: 0.3px;
    white-space: nowrap;
  }
  .contact-icon {
    width: 11px;
    height: 11px;
    flex: none;
    fill: none;
    stroke: var(--sky);
    stroke-width: 1.6;
  }
  .contact-icon.solid { fill: var(--sky); stroke: none; }
</style>
</head>
<body>
<main class="canvas">
  <section class="card card-back" role="img" aria-label="Card reverse: repeating pattern of hand-drawn white butterflies with navy outlines on sky blue"></section>

  <div class="card-row">
    <section class="card card-front card-care">
      <div class="brand">
        <span class="brand-dot"></span>
        <span class="brand-name">Brightvale Care</span>
      </div>
      <div class="divider"></div>
      <div class="contact">
        <p class="person-name">Daniel Hartley</p>
        <p class="person-role">Director</p>
        <ul class="contact-list">
          <li class="contact-item">
            <svg class="contact-icon" viewBox="0 0 14 14"><rect x="3.5" y="1" width="7" height="12" rx="1.5"/><line x1="6" y1="10.5" x2="8" y2="10.5"/></svg>
            + 61 400 218 374
          </li>
          <li class="contact-item">
            <svg class="contact-icon" viewBox="0 0 14 14"><path d="M2 5 Q7 1.5 12 5 L11 7 L9 6 L9 4.8 Q7 4 5 4.8 L5 6 L3 7 Z"/><rect x="3.5" y="7.5" width="7" height="5" rx="1"/></svg>
            + 61 (0)2 9015 4420
          </li>
          <li class="contact-item">
            <svg class="contact-icon solid" viewBox="0 0 14 14"><path d="M1 3h12v8H1z"/><path d="M1 3l6 5 6-5" fill="none" stroke="#fff" stroke-width="1.2"/></svg>
            name@brightvalecare.net.au
          </li>
          <li class="contact-item">
            <svg class="contact-icon" viewBox="0 0 14 14"><circle cx="7" cy="7" r="5.5"/><ellipse cx="7" cy="7" rx="2.3" ry="5.5"/><line x1="1.5" y1="7" x2="12.5" y2="7"/></svg>
            www.brightvalecare.net.au
          </li>
        </ul>
      </div>
    </section>

    <section class="card card-front card-hr">
      <div class="brand">
        <span class="brand-dot"></span>
        <span class="brand-name">Brightvale HR</span>
      </div>
      <div class="divider"></div>
      <div class="contact">
        <p class="person-name">Daniel Hartley</p>
        <p class="person-role">Director</p>
        <ul class="contact-list">
          <li class="contact-item">
            <svg class="contact-icon" viewBox="0 0 14 14"><rect x="3.5" y="1" width="7" height="12" rx="1.5"/><line x1="6" y1="10.5" x2="8" y2="10.5"/></svg>
            + 61 400 218 374
          </li>
          <li class="contact-item">
            <svg class="contact-icon" viewBox="0 0 14 14"><path d="M2 5 Q7 1.5 12 5 L11 7 L9 6 L9 4.8 Q7 4 5 4.8 L5 6 L3 7 Z"/><rect x="3.5" y="7.5" width="7" height="5" rx="1"/></svg>
            + 61 (0)2 9015 4420
          </li>
          <li class="contact-item">
            <svg class="contact-icon solid" viewBox="0 0 14 14"><path d="M1 3h12v8H1z"/><path d="M1 3l6 5 6-5" fill="none" stroke="#fff" stroke-width="1.2"/></svg>
            name@brightvalehr.com.au
          </li>
          <li class="contact-item">
            <svg class="contact-icon" viewBox="0 0 14 14"><circle cx="7" cy="7" r="5.5"/><ellipse cx="7" cy="7" rx="2.3" ry="5.5"/><line x1="1.5" y1="7" x2="12.5" y2="7"/></svg>
            www.brigthvalehr.com.au
          </li>
        </ul>
      </div>
    </section>
  </div>
</main>
</body>
</html>
```